New Business Card Design Project

We require a business card design for Vexalund, a newly established Indian company.
Our focus is on the development, manufacturing, and export of a diverse array of pharmaceutical products on a global scale. The card should convey a professional appearance, as our primary markets are in Africa, China, and Southeast Asian nations.
We envision a two-sided business card, with the reverse side dedicated to a logo set against a solid color or an elegantly designed pattern. The corners should be rounded. We would appreciate seeing both horizontal and vertical design options. We trust the designer to utilize their expertise in creating this design.

The content for the business card is included in the attached Word file.

Target Market(s)

Our primary markets are in Africa, China, and Southeast Asian, Latin America, Maldives, Sri Lanka

Industry/Entity Type

Pharmaceutical Manufacturing and Export

Contact Information for Business Card

Colors

Designer to choose colors to be used in the design.

Requirements
Must have
• The reverse side of the business card features solely the logo along with the tagline, "Care for Every Day."
Should not have
• The logo should not exceed two instances, encompassing both the front and back sides of the card.

```html
<!DOCTYPE html>
<html lang="en">
<head>
<meta charset="utf-8">
<title>Vexalund Business Card</title>
<link rel="stylesheet" href="https://fonts.googleapis.com/css2?family=Poppins:wght@400;600&family=Open+Sans:wght@400;700&display=swap">
<style>
  :root {
    --stage: #232323;
    --brand-blue: #2ea8df;
    --brand-coral: #f06650;
    --paper: #ffffff;
    --shadow: rgba(0, 0, 0, 0.75);
  }
  * { margin: 0; padding: 0; box-sizing: border-box; }
  html, body { width: 1200px; height: 711px; overflow: hidden; }
  body {
    background: var(--stage);
    position: relative;
    font-family: "Open Sans", sans-serif;
  }
  .card {
    position: absolute;
    left: 341px;
    width: 518px;
    height: 296px;
    border-radius: 24px;
    overflow: hidden;
    box-shadow: 0 10px 24px var(--shadow);
  }
  /* Reverse side */
  .card-back {
    top: 45px;
    background: var(--paper);
  }
  .back-wordmark {
    position: absolute;
    left: 0; right: 0;
    top: 180px;
    text-align: center;
    font-family: "Poppins", sans-serif;
    font-weight: 600;
    font-size: 52px;
    line-height: 1;
    color: var(--brand-blue);
    letter-spacing: 0.5px;
  }
  .tagline {
    position: absolute;
    left: 0; right: 0;
    top: 262px;
    text-align: center;
    font-family: "Poppins", sans-serif;
    font-size: 13px;
    color: var(--brand-blue);
  }
  /* Front side */
  .card-front {
    top: 370px;
    background: var(--brand-blue);
  }
  .front-panel {
    position: absolute;
    left: 0; top: 0;
    width: 320px; height: 296px;
  }
  .front-info {
    position: absolute;
    right: 19px;
    top: 0;
    text-align: right;
    color: var(--paper);
  }
  .front-wordmark {
    position: absolute;
    right: 0;
    top: 92px;
    font-family: "Poppins", sans-serif;
    font-weight: 600;
    font-size: 29px;
    line-height: 1;
    white-space: nowrap;
  }
  .person-name {
    position: absolute;
    right: 0;
    top: 142px;
    font-size: 23px;
    line-height: 1;
    color: var(--brand-coral);
    white-space: nowrap;
  }
  .person-name .first { font-weight: 700; }
  .person-role {
    position: absolute;
    right: 0;
    top: 168px;
    font-size: 12px;
    line-height: 1;
  }
  .address {
    position: absolute;
    right: 0;
    top: 194px;
    font-size: 12px;
    line-height: 16px;
    white-space: nowrap;
  }
  .contacts {
    position: absolute;
    right: 0;
    top: 235px;
    list-style: none;
    font-size: 12px;
    line-height: 15.5px;
    white-space: nowrap;
  }
  .contacts li { display: flex; justify-content: flex-end; align-items: center; gap: 8px; }
  .contacts svg { width: 11px; height: 11px; }
  .accent-bar {
    position: absolute;
    right: 0;
    top: 148px;
    width: 13px;
    height: 32px;
    background: var(--brand-coral);
  }
</style>
</head>
<body>
  <section class="card card-back" aria-label="Card reverse">
    <div class="back-wordmark">Vexalund</div>
    <p class="tagline">Care for Every Day.</p>
  </section>

  <section class="card card-front" aria-label="Card front">
    <svg class="front-panel" viewBox="0 0 320 296" aria-hidden="true">
      <path d="M0 0 H150 C175 40 160 70 200 120 C240 175 290 230 300 296 H0 Z" fill="var(--paper)"/>
    </svg>
    <div class="accent-bar"></div>
    <div class="front-info">
      <div class="front-wordmark">Vexalund</div>
      <div class="person-name"><span class="first">Arvind</span> K. Solanki</div>
      <div class="person-role">CEO</div>
      <p class="address">12, Nilgiri Colony,<br>Akola, 444001, India</p>
      <ul class="contacts">
        <li>+919 555010123
          <svg viewBox="0 0 12 12"><rect x="3" y="0.8" width="6" height="10.4" rx="1" fill="none" stroke="var(--brand-coral)" stroke-width="1.4"/></svg>
        </li>
        <li>www.vexalund.com
          <svg viewBox="0 0 12 12"><circle cx="6" cy="6" r="5" fill="none" stroke="var(--brand-coral)" stroke-width="1.4"/><path d="M1 6 H11 M6 1 C3 4 3 8 6 11 C9 8 9 4 6 1" fill="none" stroke="var(--brand-coral)" stroke-width="1"/></svg>
        </li>
        <li>asolanki@vexalund.com
          <svg viewBox="0 0 12 12"><rect x="0.8" y="2.5" width="10.4" height="7.5" fill="none" stroke="var(--brand-coral)" stroke-width="1.4"/><path d="M1 3 L6 7 L11 3" fill="none" stroke="var(--brand-coral)" stroke-width="1.2"/></svg>
        </li>
      </ul>
    </div>
  </section>
</body>
</html>
```